Media Services Start-up -- Corporate Website and Logo Design. Inspiration required!

We need a logo design and corporate website design, including coding, for our start-up business.
Vennatra’s value proposition is based on bringing together media content from a vast number of geographies globally, adding human and AI curation, translation and editing, and delivering the content using tailored customer interfaces. On the one hand, the business brings together media coverage from all over the world, and on the other it brings together content, human skills and technology to deliver a supreme customer experience.
Vennatra is a B2B media monitoring and analytics business with emphasis on global customers. Vennatra's service offering is centred around sourcing media content from different markets, processing, storing and delivering the content and insights derived from it using an online platform / mobile app.
The messaging we want to create through the logo is:
- Global scope
- Speed of delivery
- Cost-efficiency
- Multi-lingual
- Tailor-made
- Trustworthy
Target Market(s)
Business to business, PR / Communications, Media, Marketing
Logo Text
Vennatra
Coding
Coded - Design and coding required
Number of Pages Required
5+ page
Font styles to use
Other font styles liked:
- See Design Brief for details
Colors
Designer to choose colors to be used in the design.

```html
<!DOCTYPE html>
<html lang="en">
<head>
<meta charset="utf-8">
<title>Vennatra — Global Media Intelligence</title>
<link href="https://fonts.googleapis.com/css2?family=Roboto:ital,wght@0,400;0,500;0,700;1,400&family=Roboto+Condensed:wght@700&family=Open+Sans:wght@400&display=swap" rel="stylesheet">
<style>
:root{
  --board:#c9c9c9;
  --white:#ffffff;
  --teal:#9ecbcb;
  --teal-card:rgba(164,207,207,.88);
  --teal-soft:#d4e7e7;
  --teal-play:#9fcdcd;
  --ink:#141414;
  --muted:#6d6d6d;
  --hero-dark:#0b1a26;
}
*{margin:0;padding:0;box-sizing:border-box}
html,body{width:671px;height:1200px;overflow:hidden;background:var(--board)}
body{position:relative;font-family:'Roboto',sans-serif;color:var(--ink)}
.screen{position:absolute;left:24px;width:621px;background:var(--white);overflow:hidden}
.screen--home{top:43px;height:374px}
.screen--people{top:453px;height:696px}

/* header */
.site-header{position:absolute;left:0;top:0;width:621px;height:52px;background:var(--teal)}
.contact-bar{position:absolute;right:57px;top:0;height:19px;display:flex;align-items:center;gap:12px;font-size:7.2px;font-family:'Open Sans',sans-serif}
.contact-bar span{display:flex;align-items:center;gap:4px}
.contact-bar svg{width:7px;height:7px}
.brand{position:absolute;left:75px;top:25px;font-family:'Open Sans',sans-serif;font-size:12.5px;color:var(--ink);display:flex;align-items:center;gap:5px}
.brand i{display:block;width:6px;height:6px;border-radius:50%;background:var(--ink)}
.main-nav{position:absolute;left:168px;top:19px;width:453px;height:33px;background:var(--white);clip-path:polygon(0 0,100% 0,100% 100%,11px 100%);box-shadow:0 1px 2px rgba(0,0,0,.1)}
.main-nav a{position:absolute;top:12px;font-size:7.8px;font-weight:500;color:var(--ink);text-decoration:none;white-space:nowrap}

/* hero */
.hero-art{position:absolute;left:0;top:0}
.hero-title{position:absolute;right:57px;top:92px;text-align:right;color:var(--white);font-family:'Roboto Condensed',sans-serif;font-weight:700;font-size:23px;line-height:26.5px}
.hero-lede{position:absolute;right:57px;top:150px;width:300px;text-align:right;color:var(--white);font-size:7px;line-height:13.4px}
.btn-read{position:absolute;left:446px;top:191px;width:118px;height:22px;border-radius:11px;background:var(--ink);color:var(--white);font-size:8.4px;font-weight:700;display:flex;align-items:center;justify-content:center}
.lead-card{position:absolute;left:74px;top:112px;width:166px;height:180px;border-radius:20px;background:var(--teal-card)}
.lead-card h2{position:absolute;left:11px;top:24px;font-size:9px;font-weight:700;white-space:nowrap}
.field{position:absolute;left:11px;width:115px;height:21px;border-radius:10px;background:var(--white);font-size:7.4px;padding-left:12px;display:flex;align-items:center}
.btn-start{position:absolute;left:11px;top:138px;width:115px;height:21px;border-radius:10px;background:var(--ink);color:var(--white);font-size:7.4px;display:flex;align-items:center;justify-content:center}

/* people */
.blob{position:absolute;left:0;top:0}
.photo{position:absolute;border-radius:50%}
.photo--ceo{left:244px;top:97px;width:132px;height:132px;border:3px solid var(--white);background:radial-gradient(circle at 50% 40%,#e9c3ad 0,#d8a88f 35%,#bcd2ea 70%,#f4f6f8 100%);box-shadow:0 2px 5px rgba(0,0,0,.15)}
.section-title{position:absolute;left:0;width:621px;text-align:center;font-weight:700}
.ceo-title{top:248px;font-size:17px}
.ceo-quote{position:absolute;left:87px;top:283px;width:468px;text-align:center;font-style:italic;font-size:7.7px;line-height:13.3px}
.ceo-quote b{position:absolute;left:-4px;top:-4px;font-size:10px;font-style:italic}
.team-title{top:362px;font-size:18px}
.team-sub{position:absolute;left:0;top:394px;width:621px;text-align:center;font-size:8.6px;color:var(--muted)}
.member{position:absolute;text-align:center}
.member .name{font-size:9.2px;font-weight:500}
.member .role{font-size:7.6px;margin-top:4px}
.member-quote{position:absolute;width:142px;font-style:italic;font-size:7.7px;line-height:12.8px;text-align:justify;text-align-last:justify}
.qmark{position:absolute;font-family:Georgia,serif;font-weight:700;font-size:14px;line-height:1}
.avatar-sm{width:32px;height:32px;background:radial-gradient(circle at 50% 40%,#cfa38d 0,#b98670 40%,#e9eef1 80%)}
.avatar-lg{left:256px;top:447px;width:106px;height:106px;background:radial-gradient(circle at 50% 40%,#c99a82 0,#7a8b96 45%,#3d5868 75%,#1e2428 100%);box-shadow:0 2px 6px rgba(0,0,0,.2)}
.play{position:absolute;left:288px;top:430px;width:35px;height:35px;border-radius:50%;background:var(--teal-play);border:2px solid var(--white);display:flex;align-items:center;justify-content:center}
.dots{position:absolute;left:285px;top:618px;display:flex;gap:4px}
.dots i{display:block;width:9px;height:9px;border-radius:50%;border:1.3px solid var(--ink)}
.dots i.on{background:#7e7e7e;border-color:#7e7e7e}
.footer-note{position:absolute;left:0;top:1173px;width:671px;text-align:center;font-size:8px;color:var(--ink)}
</style>
</head>
<body>

<section class="screen screen--home">
  <svg class="hero-art" width="621" height="374" viewBox="0 0 621 374" role="img" aria-label="Photo of a hand touching a tablet with glowing app icons">
    <defs>
      <linearGradient id="heroFill" x1="0" y1="0" x2="1" y2="1">
        <stop offset="0" stop-color="#2b3440"/>
        <stop offset=".35" stop-color="#8a6a52"/>
        <stop offset=".55" stop-color="#c9924f"/>
        <stop offset=".75" stop-color="#2c4a63"/>
        <stop offset="1" stop-color="#0b1a26"/>
      </linearGradient>
    </defs>
    <path d="M90 52 L621 52 L621 211 C540 250 450 350 374 357 C300 362 270 320 244 264 Z" fill="url(#heroFill)"/>
  </svg>

  <header class="site-header">
    <div class="contact-bar">
      <span><svg viewBox="0 0 10 10"><path d="M2 1l2 2-1 1.3c.6 1.2 1.5 2.1 2.7 2.7L7 6l2 2-1.3 1.5C4.5 9.3.7 5.5.5 2.3z" fill="#141414"/></svg>555 014 2290</span>
      <span><svg viewBox="0 0 10 10"><rect x=".7" y="1.7" width="8.6" height="6.6" fill="none" stroke="#141414"/><path d="M.7 1.7L5 5.5l4.3-3.8" fill="none" stroke="#141414"/></svg>hello@vennatra.com</span>
    </div>
    <div class="brand"><i></i>Vennatra</div>
    <nav class="main-nav">
      <a style="left:24px">HOME</a><a style="left:67px">SOLUTIONS</a><a style="left:130px">HOW WE DO IT</a><a style="left:203px">OUR PEOPLE</a><a style="left:271px">OUR TECHNOLOGY</a><a style="left:359px">CONTACT</a>
    </nav>
  </header>

  <h1 class="hero-title">DELIVERING GLOBAL<br>MEDIA INTELLIGENCE</h1>
  <p class="hero-lede">Vennatra is an international media intelligence service provider. We help communications teams build and operate truly global media monitoring and measurement programmes</p>
  <div class="btn-read">READ MORE</div>

  <form class="lead-card">
    <h2>LEARN MORE ABOUT VENNATRA</h2>
    <div class="field" style="top:54px">NAME</div>
    <div class="field" style="top:80px">EMAIL</div>
    <div class="field" style="top:107px">PHONE</div>
    <div class="btn-start">GET STARTED</div>
  </form>
</section>

<section class="screen screen--people">
  <svg class="blob" width="621" height="696" viewBox="0 0 621 696" aria-hidden="true">
    <path d="M0 275 C40 230 150 200 245 146 C300 115 330 100 380 103 C500 115 570 250 575 390 C580 520 560 580 500 600 C420 620 350 640 300 641 C220 642 180 630 160 600 C110 520 40 420 0 338 Z" fill="#d4e7e7"/>
    <path d="M298 630 L322 630 L310 643 Z" fill="#9ecbcb"/>
  </svg>

  <header class="site-header">
    <div class="contact-bar">
      <span><svg viewBox="0 0 10 10"><path d="M2 1l2 2-1 1.3c.6 1.2 1.5 2.1 2.7 2.7L7 6l2 2-1.3 1.5C4.5 9.3.7 5.5.5 2.3z" fill="#141414"/></svg>555 014 2290</span>
      <span><svg viewBox="0 0 10 10"><rect x=".7" y="1.7" width="8.6" height="6.6" fill="none" stroke="#141414"/><path d="M.7 1.7L5 5.5l4.3-3.8" fill="none" stroke="#141414"/></svg>hello@vennatra.com</span>
    </div>
    <div class="brand"><i></i>Vennatra</div>
    <nav class="main-nav">
      <a style="left:24px">HOME</a><a style="left:67px">SOLUTIONS</a><a style="left:130px">HOW WE DO IT</a><a style="left:203px">OUR PEOPLE</a><a style="left:271px">OUR TECHNOLOGY</a><a style="left:359px">CONTACT</a>
    </nav>
  </header>

  <div class="photo photo--ceo" role="img" aria-label="Portrait of the chief executive"></div>
  <h2 class="section-title ceo-title">OUR CEO</h2>
  <p class="ceo-quote"><b>“</b>Lorem ipsum dolor sit amet, consectetur adipiscing elit, sed do eiusmod tempor incididunt ut labore et dolore magna aliqua. Quis ipsum suspendisse ultrices gravida. Risus commodo viverra maecenas accumsan lacus vel facilisis. Lorem ipsum dolor sit amet, consectetur adipiscing elit, sed do eiusmod tempor incididunt ut labore et dolore</p>

  <h2 class="section-title team-title">What Our Team Say About us</h2>
  <p class="team-sub">25 Thousand + Customers From All Over World</p>

  <div class="photo avatar-sm" style="left:125px;top:431px" role="img" aria-label="Portrait of Marcus Halden"></div>
  <div class="member" style="left:71px;top:473px;width:142px"><div class="name">MARCUS HALDEN</div><div class="role">CREATIVE DIRECTOR</div></div>
  <span class="qmark" style="left:68px;top:495px">“</span>
  <p class="member-quote" style="left:74px;top:510px">Lorem ipsum dolor sit amet, consectetur adipiscing elit, sed do eiusmod tempor incididunt ut labore et dolore magna aliqua. Quis ipsum suspendisse ultrices gravida. Risus commodo viverra</p>

  <div class="photo avatar-lg" role="img" aria-label="Portrait of Elena Brisk"></div>
  <div class="play"><svg width="10" height="10" viewBox="0 0 10 10"><circle cx="5" cy="5" r="4.2" fill="none" stroke="#141414" stroke-width="1.1"/><path d="M4 3l3 2-3 2z" fill="#141414"/></svg></div>
  <div class="member" style="left:238px;top:581px;width:142px"><div class="name">ELENA BRISK</div><div class="role">COO</div></div>
  <div class="dots"><i></i><i></i><i class="on"></i><i></i></div>

  <div class="photo avatar-sm" style="left:473px;top:431px" role="img" aria-label="Portrait of Nadia Orrel"></div>
  <div class="member" style="left:419px;top:474px;width:142px"><div class="name">NADIA ORREL</div><div class="role">ASST. MANAGER</div></div>
  <span class="qmark" style="left:413px;top:498px">“</span>
  <p class="member-quote" style="left:421px;top:511px">Lorem ipsum dolor sit amet, consectetur adipiscing elit, sed do eiusmod tempor incididunt ut labore et dolore magna aliqua. Quis ipsum suspendisse ultrices gravida. Risus commodo viverra</p>
</section>

<p class="footer-note">© COPY RIGHTS @ ALL RIGHTS RESERVED</p>

</body>
</html>
```